Coaches and Student-Athlete Led Services Business Needs a Business Card Design

Quarterline Aid is an award-winning household services company, uniquely Guided By Mentors & Fueled By Varsity Players. We aim to bring excellence and community spirit to every service we provide.

Objective
We need a professional, eye-catching business card design that aligns with our brand identity and communicates our commitment to quality service. The card should be distinct, easy to read, and should reflect our values as a Veteran and Women-Owned business.

Specifications

Front Side Requirements
- Background Color: The background should complement our new Quarterline Aid’s brand colors (see attached logo artwork file), creating a cohesive and vibrant look.
- Branding: Display our logo and tagline prominently. (Files attached)
- Contact Details: Include fields for name, title, phone number, and email address.

Back Side Requirements
- Background Color: Maintain brand consistency with a complementary background color.
- Logo Only: Feature the logo alone, without the tagline, for brand recognition.
- Contact Details: Clearly display the company’s website, main phone number, and customer service email.
- QR Code: Include a QR code that links directly to our website (www.quarterlineaid-example.com), enabling easy access to our online resources and service options.

Optional Additions (Include if space allows or if it enhances the design):

Business Accolades and Identity:
- Use icons or text to denote "Veteran & Women-Owned" to highlight our business heritage.
- Highlight “Local Champions Always Get 10% Off” with a prompt like “See if you qualify” for community-driven appeal.

Awards and Recognition:
- Consider incorporating award symbols or icons, such as Porchlane Pick, Top of the Town, and Sterling Trade Prize, to showcase our reputation for excellence. (Award icons are available at quarterlineaid-example.com/trophy-case.)

Design Notes
Shape and Size: We are open to non-traditional shapes that follow standard print guidelines, such as rounded corners, vertical orientation, or other custom shapes, as long as they suit the design.

Tone and Style: The card should feel professional and friendly, reflecting our brand's commitment to high-quality service with a community-oriented, approachable style.

```html
<!DOCTYPE html>
<html lang="en">
<head>
<meta charset="utf-8">
<title>Quarterline Aid Business Card</title>
<link rel="stylesheet" href="https://fonts.googleapis.com/css2?family=Poppins:wght@600;700&family=Roboto:wght@400;500;700&display=swap">
<style>
  :root {
    --navy: #1b2a6b;
    --red: #c8173a;
    --purple: #5a2a7a;
    --paper: #f7f7f5;
    --ink: #3c3c3c;
    --muted: #666;
    --stage: #2c2c2c;
    --badge-green: #7cc242;
    --badge-dark: #2f4f3a;
  }
  * { margin: 0; padding: 0; box-sizing: border-box; }
  html, body { width: 1200px; height: 852px; overflow: hidden; }
  body {
    background: var(--stage);
    font-family: "Roboto", Arial, sans-serif;
    position: relative;
  }
  .card {
    position: absolute;
    width: 520px;
    height: 300px;
    background: var(--paper);
    border-radius: 28px;
    overflow: hidden;
    box-shadow: 0 14px 30px rgba(0,0,0,.45);
    border-bottom: 4px solid var(--red);
  }
  .card--front { left: 50px; top: 276px; }
  .card--back { left: 630px; top: 276px; }

  /* Front */
  .brand-row {
    position: absolute; left: 40px; top: 48px;
    display: flex; align-items: center; gap: 14px;
  }
  .brand-dot {
    width: 46px; height: 46px; border-radius: 50%;
    border: 4px solid var(--red); background: var(--paper);
  }
  .brand-name {
    font-family: "Poppins", Arial, sans-serif;
    font-weight: 700; font-size: 42px; color: var(--navy);
    letter-spacing: -.5px;
  }
  .contact-row {
    position: absolute; left: 40px; top: 132px;
    display: flex; gap: 18px; font-size: 12px; color: var(--navy);
  }
  .contact-row span { display: flex; align-items: center; gap: 6px; white-space: nowrap; }
  .owned-band {
    position: absolute; left: 0; top: 160px; width: 100%; height: 30px;
    background: linear-gradient(90deg, var(--red) 0%, var(--purple) 55%, var(--navy) 100%);
    display: flex; align-items: center; padding-left: 150px;
    color: #fff; font-weight: 700; font-size: 15px;
  }
  .promo-row {
    position: absolute; left: 40px; right: 28px; top: 208px;
    display: flex; align-items: center; justify-content: space-between;
  }
  .promo-pill {
    padding: 6px 18px; border: 2px solid var(--navy); border-radius: 20px;
    color: var(--navy); font-weight: 700; font-size: 14px; background: #fff;
    white-space: nowrap;
  }
  .badge-row { display: flex; gap: 6px; }
  .badge { width: 20px; height: 20px; border-radius: 50%; background: var(--badge-green); }
  .badge--dark { background: var(--badge-dark); }
  .front-footer {
    position: absolute; left: 0; bottom: 0; width: 100%; height: 30px;
    background: var(--red);
  }

  /* Back */
  .seal {
    position: absolute; left: 36px; top: 46px;
    width: 180px; height: 180px; border-radius: 50%;
    border: 6px solid var(--red);
    display: flex; align-items: center; justify-content: center;
    text-align: center;
  }
  .seal-name {
    font-family: "Poppins", Arial, sans-serif; font-weight: 700;
    font-size: 22px; line-height: 1.1; color: var(--navy);
  }
  .person { position: absolute; left: 270px; top: 46px; }
  .person-name { color: var(--red); font-weight: 700; font-size: 19px; }
  .person-title { color: var(--muted); font-size: 11px; margin-top: 2px; }
  .contact-list { list-style: none; margin-top: 18px; font-size: 11.5px; color: var(--ink); }
  .contact-list li { display: flex; align-items: flex-start; gap: 8px; line-height: 1.45; }
  .contact-list svg { flex: none; margin-top: 3px; }
  .contact-list .address { margin-top: 6px; padding-left: 20px; }
  .back-footer { position: absolute; left: 0; bottom: 0; width: 100%; height: 44px; }
  .footer-offer {
    position: absolute; left: 0; top: 0; height: 100%; width: 380px;
    background: var(--navy); color: #fff; font-weight: 500; font-size: 13px;
    display: flex; align-items: center; padding-left: 28px;
  }
  .footer-owned {
    position: absolute; right: 0; top: -40px; height: 84px; width: 170px;
    background: var(--red); color: #fff; font-size: 12px;
    clip-path: polygon(18% 0, 100% 0, 100% 100%, 0 100%);
    display: flex; align-items: flex-start; justify-content: center; padding: 12px 0 0 26px;
  }
</style>
</head>
<body>

<section class="card card--front" aria-label="Front of card">
  <div class="brand-row">
    <div class="brand-dot"></div>
    <div class="brand-name">Quarterline Aid</div>
  </div>
  <div class="contact-row">
    <span>
      <svg width="12" height="9" viewBox="0 0 12 9"><rect width="12" height="9" rx="1" fill="#c8173a"/><path d="M0 0 L6 5 L12 0" stroke="#fff" fill="none"/></svg>
      service@quarterlineaid-example.com
    </span>
    <span>
      <svg width="11" height="11" viewBox="0 0 11 11"><circle cx="5.5" cy="5.5" r="5" fill="#c8173a"/><path d="M0.5 5.5 H10.5 M5.5 0.5 V10.5" stroke="#fff" stroke-width="0.8"/></svg>
      www.quarterlineaid-example.com
    </span>
  </div>
  <div class="owned-band">Veteran &amp; Women-Owned</div>
  <div class="promo-row">
    <div class="promo-pill">Local Champions Always Get 10% Off</div>
    <div class="badge-row" role="img" aria-label="Award and listing badges">
      <div class="badge"></div>
      <div class="badge"></div>
      <div class="badge badge--dark"></div>
      <div class="badge"></div>
      <div class="badge badge--dark"></div>
      <div class="badge badge--dark"></div>
    </div>
  </div>
  <div class="front-footer"></div>
</section>

<section class="card card--back" aria-label="Back of card">
  <div class="seal">
    <div class="seal-name">Quarterline<br>Aid</div>
  </div>
  <div class="person">
    <div class="person-name">Evan Marlowe</div>
    <div class="person-title">Owner / Founder / Coach</div>
    <ul class="contact-list">
      <li>
        <svg width="12" height="12" viewBox="0 0 12 12"><path d="M2 1 L4 1 L5 4 L3.5 5 C4.3 7 5 7.7 7 8.5 L8 7 L11 8 L11 10 C11 11 10 11 9 11 C4.5 10.5 1.5 7.5 1 3 C1 2 1 1 2 1Z" fill="#c8173a"/></svg>
        <span>(555) PRO-YARD<br>(555) 014-2287</span>
      </li>
      <li>
        <svg width="12" height="9" viewBox="0 0 12 9"><rect width="12" height="9" rx="1" fill="#c8173a"/><path d="M0 0 L6 5 L12 0" stroke="#fff" fill="none"/></svg>
        <span>service@quarterlineaid-example.com</span>
      </li>
      <li>
        <svg width="11" height="11" viewBox="0 0 11 11"><circle cx="5.5" cy="5.5" r="5" fill="#c8173a"/><path d="M0.5 5.5 H10.5 M5.5 0.5 V10.5" stroke="#fff" stroke-width="0.8"/></svg>
        <span>www.quarterlineaid-example.com</span>
      </li>
      <li class="address"><span>4870 N Alder Way, Unit 12,<br>Ridgefield, CO 80000</span></li>
    </ul>
  </div>
  <div class="back-footer">
    <div class="footer-owned">Veteran &amp; Women-Owned</div>
    <div class="footer-offer">Local Champions Always Get 10% OFF</div>
  </div>
</section>

</body>
</html>
```